VL - menu design

Hi,

We require elegant menu design for upscale restaurant. Please find attached the logo and the menu items for your reference.

for inspiration, this is a good website: -
http://www.plateworthy-sample.net/dishcraft/about.php

We are very much open for Menu Size suggestions.

unfortunately the place is going under renovation, we don't have updated images to it. the closest look and feel to our place is http://vazelo-example.com ..

we are also open for creative options on the shape, the styles, etc. as long as it represents the fine dine feel ...

Thanks ...

Dear All,

We wouldlike to extend our apology for not being able to provide feedbacks on everysingle design. We were extremely busy and we have multiple contests opensimultaneously which makes the process even harder.

However,we would like to thank you all for the efforts you have put into designingour menu. It is very much appreciated …

We wishyou all success in your design ventures and we are quite positive that we willbe working with many of you on many projects in the soon future. 

Thanks & Regards,

DQI Team...

 

 

 

Industry/Entity Type

Restaurant

Requirements
Must have
• Please ensure that there are 'some' images in the menu ... this is very important.
Should not have
• IMPORTANT: -

1. Please DO NOT insert any currency sign to the menu
2. Please keep the prices of the menu at the end of the menu items descriptions NOT beside the menu item names. The font of the price should be similar to the menu item description and please DO NOT bold the numbers. the prices should be subtle.

Thank you ...

```html
<!DOCTYPE html>
<html lang="en">
<head>
<meta charset="utf-8">
<title>Vela Lane Café – Menu Cover</title>
<link rel="stylesheet" href="https://fonts.googleapis.com/css2?family=Exo+2:wght@300&display=swap">
<style>
  :root {
    --cover-brown: #8b7150;
    --disc-white: #f0f0f0;
    --rule-cream: #eadfcd;
    --ink-dark: #161616;
    --label-tan: #8b7150;
  }
  html, body {
    margin: 0;
    padding: 0;
    width: 1200px;
    height: 2700px;
    overflow: hidden;
    background: var(--cover-brown);
  }
  .menu-cover {
    position: relative;
    width: 1200px;
    height: 2700px;
    background: var(--cover-brown);
    font-family: "Exo 2", sans-serif;
    font-weight: 300;
  }
  .cover-art {
    position: absolute;
    inset: 0;
  }
  .guide-dashed {
    stroke: var(--rule-cream);
    stroke-width: 2;
    stroke-dasharray: 12 9;
  }
  .guide-solid {
    stroke: var(--rule-cream);
    stroke-width: 3;
  }
  .disc { fill: var(--disc-white); }

  .brand-name {
    position: absolute;
    left: 116px;
    top: 968px;
    width: 960px;
    margin: 0;
    text-align: center;
    color: var(--ink-dark);
    font-family: "Exo 2", sans-serif;
    font-weight: 300;
    line-height: 1;
  }
  .brand-name .brand-line {
    display: block;
    font-size: 104px;
    letter-spacing: 0.24em;
    padding-left: 0.24em;
    white-space: nowrap;
  }
  .brand-name .brand-sub {
    display: block;
    font-size: 34px;
    letter-spacing: 0.9em;
    padding-left: 0.9em;
    margin-top: 34px;
  }
  .menu-label {
    position: absolute;
    left: 376px;
    top: 2262px;
    width: 444px;
    margin: 0;
    text-align: center;
    color: var(--label-tan);
    font-family: "Exo 2", sans-serif;
    font-weight: 300;
    font-size: 92px;
    line-height: 1;
    letter-spacing: 0.01em;
  }
</style>
</head>
<body>
  <main class="menu-cover">
    <svg class="cover-art" width="1200" height="2700" viewBox="0 0 1200 2700" aria-hidden="true">
      <g class="guides">
        <line class="guide-dashed" x1="316" y1="0" x2="316" y2="2700"/>
        <line class="guide-dashed" x1="456" y1="0" x2="456" y2="2700"/>
        <line class="guide-dashed" x1="740" y1="0" x2="740" y2="2700"/>
        <line class="guide-dashed" x1="880" y1="0" x2="880" y2="2700"/>
        <line class="guide-solid" x1="600" y1="0" x2="600" y2="500"/>
        <line class="guide-solid" x1="600" y1="1560" x2="600" y2="2100"/>
      </g>
      <circle class="disc disc-brand" cx="596" cy="1030" r="540"/>
      <circle class="disc disc-label" cx="598" cy="2310" r="222"/>
    </svg>

    <h1 class="brand-name">
      <span class="brand-line">VELA LANE</span>
      <span class="brand-sub">CAFÉ</span>
    </h1>

    <p class="menu-label">Menu</p>
  </main>
</body>
</html>
```